Blind Rivet Product catalogue

Need a design in wordpress with a productcatalogue where i present all products. This is a B2B business. The products is Blindrivets and Blindrivet nuts and accessories to this. I only want the basic information and also technical specification.

This is a subcompany to my existing company k7.m3.se but specializing in a subcategory

Businesses using blind rivet technology.

Industrial

Sans Serif

Must have
• Three different categories for the products; Blind Rivets - Blind Rivet Nut - Riveting Tools
Nice to have
• Possible to ad login for more information of the different sizes

```html
<!DOCTYPE html>
<html lang="en">
<head>
<meta charset="utf-8">
<title>K7M3 – Blind Rivet Catalogue</title>
<link href="https://fonts.googleapis.com/css2?family=Outfit:wght@300;400;500;600;700&display=swap" rel="stylesheet">
<style>
:root{
  --blue:#0b93d5;
  --blue-dark:#0579b8;
  --orange:#ec6a21;
  --ink:#222;
  --muted:#777;
  --footer:#efefef;
  --line:#d8d8d8;
}
*{margin:0;padding:0;box-sizing:border-box}
html,body{width:1200px;height:2784px;overflow:hidden;background:#fff}
body{position:relative;font-family:"Outfit",sans-serif;color:var(--ink)}
.abs{position:absolute}
/* header */
.logo{left:114px;top:7px;width:105px;height:81px;background:#111;display:flex;align-items:center;justify-content:center;color:#fff;font-weight:600;font-size:22px;letter-spacing:1px}
.search{left:422px;top:37px;width:357px;height:37px;border:1px solid #ddd;display:flex}
.search span{flex:1;padding-left:19px;line-height:35px;font-size:14px;color:#999}
.search .go{width:58px;background:var(--blue);display:flex;align-items:center;justify-content:center}
.phone{left:856px;top:42px;display:flex;align-items:center;gap:12px;font-size:20px;color:#333}
.cart{left:1053px;top:37px;width:35px;height:35px;border-radius:50%;background:var(--blue);display:flex;align-items:center;justify-content:center}
.cart b{position:absolute;top:-4px;right:-2px;font-size:10px;font-weight:500;color:#333}
.nav{left:0;top:93px;width:1200px;height:48px;background:linear-gradient(#19aee8,#0588c9)}
.nav a{position:absolute;top:0;line-height:48px;color:#fff;font-size:16px;text-decoration:none;font-weight:500}
.nav .home{left:196px;width:82px;text-align:center;background:var(--orange)}
/* hero */
.hero{left:0;top:141px;width:1200px;height:556px;background:linear-gradient(110deg,#2b3440 0%,#4a5564 45%,#6b737c 70%,#3b3c3e 100%)}
.hero h1{position:absolute;left:108px;top:152px;font-size:94px;font-weight:700;color:#fff;letter-spacing:-2px;line-height:1}
.hero p{position:absolute;left:112px;top:255px;width:580px;font-size:16px;line-height:32px;color:#fff}
.pill{display:inline-block;background:var(--blue);color:#fff;border-radius:30px;text-align:center;font-weight:500}
.hero .pill{position:absolute;left:114px;top:329px;width:154px;height:51px;line-height:51px;font-size:16px}
.dots{position:absolute;left:554px;top:524px;display:flex;gap:12px}
.dots i{width:14px;height:12px;border:1px solid #fff;display:block}
.dots i.on{background:var(--orange);border-color:var(--orange)}
/* sections */
.h2{left:0;width:1200px;text-align:center;font-size:44px;font-weight:700;letter-spacing:-1px}
.card{top:875px;width:318px;height:412px;background:#fff;box-shadow:0 0 6px rgba(0,0,0,.18)}
.card .photo{position:absolute;left:30px;top:30px;width:240px;height:170px;background:radial-gradient(circle,#d0d2d4 0%,#f1f1f1 55%,#fff 75%)}
.card .ic{position:absolute;right:16px;width:26px;height:26px;border:1px solid #bbb;border-radius:50%;display:flex;align-items:center;justify-content:center}
.card h3{position:absolute;left:13px;top:252px;font-size:22px;font-weight:400}
.card .stars{position:absolute;left:13px;top:286px;color:var(--orange);font-size:12px;letter-spacing:4px}
.card .price{position:absolute;left:13px;top:307px;font-size:23px;font-weight:600;color:var(--orange)}
.card .pill{position:absolute;left:14px;top:344px;width:129px;height:43px;line-height:43px;font-size:16px}
.popular{left:0;top:1393px;width:1200px;height:316px}
.popular h2{position:absolute;left:540px;top:40px;color:#fff;font-size:42px;font-weight:700}
.popular p{position:absolute;left:542px;top:101px;width:545px;color:#fff;font-size:16px;line-height:34px;font-weight:300}
.popular a{position:absolute;left:548px;top:244px;color:#fff;font-size:16px}
.news{top:1874px;width:321px}
.news .photo{height:237px}
.news h4{margin:24px 2px 0;font-size:16px;font-weight:400;line-height:26px}
.news .meta{margin:12px 2px 0;font-size:17px;color:#444;display:flex;gap:10px;align-items:center}
.news p{margin:12px 1px 0;font-size:16px;line-height:26px;color:var(--muted);font-weight:300}
.news .pill{margin:12px 2px 0;width:120px;height:38px;line-height:38px;font-size:15px}
.footer{left:0;top:2432px;width:1200px;height:352px;background:var(--footer)}
.col{top:62px}
.col h5{font-size:16px;font-weight:500;margin-bottom:20px}
.col a{display:block;font-size:16px;color:var(--muted);font-weight:300;line-height:37px;text-decoration:none}
.field{left:840px;top:108px;width:249px;height:45px;border:1px solid #333;background:#fff;font-size:14px;color:#777;padding-left:9px;line-height:43px}
.subscribe{left:841px;top:168px;width:136px;height:43px;background:var(--blue);color:#fff;font-size:16px;text-align:center;line-height:43px}
.cards{left:841px;top:236px;display:flex;gap:5px}
.cards i{width:36px;height:22px;display:block;border-radius:2px}
.rule{left:112px;top:294px;width:978px;border-top:1px solid #bbb}
.copy{left:0;top:312px;width:1200px;text-align:center;font-size:16px;color:var(--muted);font-weight:300}
</style>
</head>
<body>
<div class="abs logo">K7M3</div>
<div class="abs search"><span>Search</span><div class="go"><svg width="16" height="16" viewBox="0 0 16 16"><circle cx="7" cy="7" r="5" fill="none" stroke="#fff" stroke-width="1.6"/><path d="M11 11l4 4" stroke="#fff" stroke-width="1.6"/></svg></div></div>
<div class="abs phone"><svg width="18" height="18" viewBox="0 0 24 24"><path d="M6 2l4 4-2 3c1 3 4 6 7 7l3-2 4 4-3 3C10 21 3 14 3 5z" fill="none" stroke="#ec6a21" stroke-width="1.6"/></svg>555-010-2040</div>
<div class="abs cart"><svg width="18" height="16" viewBox="0 0 18 16"><path d="M1 2h3l2 8h9l2-6H5" fill="none" stroke="#fff" stroke-width="1.5"/><circle cx="7" cy="13" r="1.3" fill="#fff"/><circle cx="14" cy="13" r="1.3" fill="#fff"/></svg><b>0</b></div>

<nav class="abs nav">
  <a class="home">HOME</a>
  <a style="left:313px">ABOUT</a>
  <a style="left:421px">PRODUCTS</a>
  <a style="left:560px">BLOGS</a>
  <a style="left:666px">TESTIMONIALS</a>
  <a style="left:833px">CONTACT</a>
  <a style="left:933px"><svg width="13" height="13" viewBox="0 0 13 13" style="vertical-align:-1px;margin-right:7px"><circle cx="6.5" cy="3.5" r="3" fill="#fff"/><path d="M0 13c0-4 3-6 6.5-6S13 9 13 13z" fill="#fff"/></svg>LOG IN</a>
</nav>

<section class="abs hero" role="img" aria-label="Laser cutter head cutting sheet metal with sparks">
  <h1>BLIND RIVET</h1>
  <p>Nemo enim ipsam voluptatem quia voluptas sit aspernatur aut odit aut fugit, sed quia consequuntur magni dolores</p>
  <span class="pill">SHOP NOW</span>
  <div class="dots"><i></i><i></i><i class="on"></i><i></i></div>
</section>

<h2 class="abs h2" style="top:788px">FEATURED PRODUCTS</h2>

<div class="abs card" style="left:114px">
  <div class="photo" role="img" aria-label="Blind rivet product photo"></div>
  <div class="ic" style="top:18px"><svg width="14" height="9" viewBox="0 0 14 9"><ellipse cx="7" cy="4.5" rx="6" ry="3.5" fill="none" stroke="#333"/><circle cx="7" cy="4.5" r="1.6" fill="#333"/></svg></div>
  <div class="ic" style="top:52px"><svg width="12" height="11" viewBox="0 0 12 11"><path d="M6 10L1 5a2.7 2.7 0 015-3 2.7 2.7 0 015 3z" fill="none" stroke="#333"/></svg></div>
  <h3>BLIND RIVETS</h3><div class="stars">★★★★★</div><div class="price">$45.00</div><span class="pill">BUY NOW</span>
</div>
<div class="abs card" style="left:443px">
  <div class="photo" role="img" aria-label="Blind rivet nut product photo"></div>
  <div class="ic" style="top:18px"><svg width="14" height="9" viewBox="0 0 14 9"><ellipse cx="7" cy="4.5" rx="6" ry="3.5" fill="none" stroke="#333"/><circle cx="7" cy="4.5" r="1.6" fill="#333"/></svg></div>
  <div class="ic" style="top:52px"><svg width="12" height="11" viewBox="0 0 12 11"><path d="M6 10L1 5a2.7 2.7 0 015-3 2.7 2.7 0 015 3z" fill="none" stroke="#333"/></svg></div>
  <h3>BLIND RIVET NUT</h3><div class="stars">★★★★★</div><div class="price">$45.00</div><span class="pill">BUY NOW</span>
</div>
<div class="abs card" style="left:772px">
  <div class="photo" role="img" aria-label="Cordless riveting tool product photo"></div>
  <div class="ic" style="top:18px"><svg width="14" height="9" viewBox="0 0 14 9"><ellipse cx="7" cy="4.5" rx="6" ry="3.5" fill="none" stroke="#333"/><circle cx="7" cy="4.5" r="1.6" fill="#333"/></svg></div>
  <div class="ic" style="top:52px"><svg width="12" height="11" viewBox="0 0 12 11"><path d="M6 10L1 5a2.7 2.7 0 015-3 2.7 2.7 0 015 3z" fill="none" stroke="#333"/></svg></div>
  <h3>RIVETING TOOLS</h3><div class="stars">★★★★★</div><div class="price">$45.00</div><span class="pill">BUY NOW</span>
</div>

<section class="abs popular">
  <svg class="abs" width="1200" height="316" style="left:0;top:0">
    <defs><linearGradient id="bg-blue" x1="0" x2="1"><stop offset="0" stop-color="#0f8fd0"/><stop offset="1" stop-color="#1ea3dd"/></linearGradient></defs>
    <rect width="1200" height="316" fill="url(#bg-blue)"/>
    <polygon points="0,0 508,0 440,316 0,316" fill="#ec6a21"/>
    <polygon points="508,0 512,0 444,316 440,316" fill="#fff"/>
  </svg>
  <div class="abs" role="img" aria-label="Riveting tool and rivet nut product photo" style="left:90px;top:40px;width:280px;height:240px;border-radius:50%;background:radial-gradient(circle,rgba(40,40,50,.55),rgba(236,106,33,0) 70%)"></div>
  <h2>POPULAR PRODUCT</h2>
  <p>Nemo enim ipsam voluptatem quia voluptas sit aspernatur aut odit aut fugit, sed quia consequuntur magni dolores eos qui ratione voluptatem sequi nesciunt. Neque porro quisquam est, qui dolorem ipsum quia dolor sit amet, consectetur, Nemo enim ipsam voluptatem</p>
  <a>SHOP NOW</a>
</section>

<h2 class="abs h2" style="top:1798px">LATEST NEWS</h2>

<article class="abs news" style="left:111px">
  <div class="photo" role="img" aria-label="Engineer reviewing plans in a factory" style="background:linear-gradient(135deg,#c9d3dc,#5a86b4 60%,#8d9aa6)"></div>
  <h4>LOREM IPSUM DOLOR SIT AMET, CONSECTETUR</h4>
  <div class="meta">▦ 28/03/20 &nbsp; ✎ 125</div>
  <p>Sed ut perspiciatis unde omnis iste natus error sit voluptatem accusantium</p>
  <span class="pill">READ MORE</span>
</article>
<article class="abs news" style="left:441px">
  <div class="photo" role="img" aria-label="Hand using a tablet beside a robot arm" style="background:linear-gradient(135deg,#1d3a6a,#3b6aa8 55%,#9aa8b8)"></div>
  <h4>LOREM IPSUM DOLOR SIT AMET, CONSECTETUR</h4>
  <div class="meta">▦ 28/03/20 &nbsp; ✎ 125</div>
  <p>Sed ut perspiciatis unde omnis iste natus error sit voluptatem accusantium</p>
  <span class="pill">READ MORE</span>
</article>
<article class="abs news" style="left:770px">
  <div class="photo" role="img" aria-label="Automated production line machinery" style="background:linear-gradient(135deg,#a7c4dc,#2f6fb0 50%,#c7d6e3)"></div>
  <h4>LOREM IPSUM DOLOR SIT AMET, CONSECTETUR</h4>
  <div class="meta">▦ 28/03/20 &nbsp; ✎ 125</div>
  <p>Sed ut perspiciatis unde omnis iste natus error sit voluptatem accusantium</p>
  <span class="pill">READ MORE</span>
</article>

<footer class="abs footer">
  <div class="abs col" style="left:110px"><h5>CUSTOMER SERVICE</h5><a>Your Account</a><a>Shipping / Handling</a><a>Contact Us</a><a>Customer Review</a><a>Return Policy</a></div>
  <div class="abs col" style="left:370px"><h5>INFORMATION</h5><a>Find In Store</a><a>Business Inquiries</a></div>
  <div class="abs col" style="left:592px"><h5>GENERAL INFORMATION</h5><a>Faqs</a><a>Safe Data Sheet</a><a>Direction For Uses</a><a>Product Ingredients</a><a>Join The Team</a></div>
  <div class="abs col" style="left:841px"><h5>NEWSLETTER</h5></div>
  <div class="abs field">Enter Name</div>
  <div class="abs subscribe">SUBSCRIBE</div>
  <div class="abs cards"><i style="background:#e0552a"></i><i style="background:#1a3d8f"></i><i style="background:#2a7dc8"></i><i style="background:#9a9a9a"></i></div>
  <div class="abs rule"></div>
  <div class="abs copy">copyrights © 2020 All Rights Reserved</div>
</footer>
</body>
</html>
```